Veranix - Solution provider in business consulting

Veranix is a swiss based company providing solutions for developing markets. The business covers various fields of business consulting, such as supply chain, product costs, quality management and manufacturing management. The Business operates in a efficient, straight and solution oriented manner.
The final design should communicate these characteristics. Asian people as well as as western people shall identify the qualities of the company at first sight.
The customer needs business cards with a simple view but an recognizable design, printed in high quality. Engraved elements such as the globe or simple words are possible.
Available colors are: (RAL)
102/102/102
51/102/102
153/204/153
255/102/51
Font: Calibri

```html
<!DOCTYPE html>
<html lang="en">
<head>
<meta charset="utf-8">
<title>Veranix – Business Card</title>
<link href="https://fonts.googleapis.com/css2?family=Carlito:wght@400;700&display=swap" rel="stylesheet">
<style>
  :root {
    --page: #e4e2de;
    --card: #0b0b0b;
    --ink: #ffffff;
    --ink-soft: #d9d9d9;
  }
  html, body {
    margin: 0;
    width: 1200px;
    height: 1022px;
    overflow: hidden;
    background: var(--page);
  }
  .canvas {
    position: relative;
    width: 1200px;
    height: 1022px;
    display: flex;
    align-items: center;
    justify-content: center;
  }
  .card {
    position: relative;
    width: 900px;
    height: 514px;
    background: var(--card);
    border-radius: 22px;
    overflow: hidden;
    font-family: "Carlito", "Calibri", sans-serif;
    color: var(--ink);
  }
  .card__emblem {
    position: absolute;
    left: 520px;
    top: -110px;
    width: 400px;
    height: 400px;
    border-radius: 50%;
    background: var(--ink);
  }
  .card__divider {
    position: absolute;
    left: 470px;
    top: 0;
    bottom: 0;
    width: 1px;
    background: var(--ink-soft);
  }
  .brand {
    position: absolute;
    left: 64px;
    top: 96px;
    display: flex;
    align-items: center;
    gap: 18px;
  }
  .brand__name {
    font-size: 88px;
    font-weight: 400;
    letter-spacing: 1px;
    line-height: 1;
  }
  .brand__dot {
    width: 22px;
    height: 22px;
    border-radius: 50%;
    background: var(--ink);
  }
  .contact {
    position: absolute;
    left: 64px;
    top: 236px;
  }
  .contact__name {
    font-size: 30px;
    line-height: 36px;
    font-weight: 700;
    margin: 0 0 4px;
  }
  .contact__line {
    font-size: 19px;
    line-height: 24px;
    color: var(--ink-soft);
    margin: 0;
  }
  .contact__rule {
    width: 300px;
    height: 1px;
    background: var(--ink-soft);
    margin: 10px 0 8px;
  }
  .contact__row {
    display: flex;
    align-items: center;
    gap: 12px;
    font-size: 19px;
    line-height: 24px;
    color: var(--ink-soft);
  }
  .contact__row svg {
    width: 15px;
    height: 15px;
    flex: none;
  }
</style>
</head>
<body>
<main class="canvas">
  <section class="card" aria-label="Veranix business card">
    <div class="card__emblem"></div>
    <div class="card__divider"></div>

    <div class="brand">
      <span class="brand__name">Veranix</span>
      <span class="brand__dot"></span>
    </div>

    <div class="contact">
      <p class="contact__name">Marco Lindt</p>
      <p class="contact__line">CEO</p>
      <p class="contact__line">Veranix GmbH Feldmatt</p>
      <p class="contact__line">14 8734 Talwil Switzerland</p>
      <div class="contact__rule"></div>
      <div class="contact__row">
        <svg viewBox="0 0 16 16" fill="none" stroke="currentColor" stroke-width="1.5"><rect x="4" y="1" width="8" height="14" rx="1.5"/><line x1="7" y1="12.5" x2="9" y2="12.5"/></svg>
        <span>+41 79 382 5710</span>
      </div>
      <div class="contact__row">
        <svg viewBox="0 0 16 16" fill="currentColor"><path d="M3.5 1.5l2.5 0 1 3.5-1.6 1.2c.8 1.8 2.2 3.2 4 4l1.2-1.6 3.4 1v2.6c0 .9-.8 1.5-1.6 1.4C6.8 13.1 2.9 9.2 2.1 3.1 2 2.3 2.6 1.5 3.5 1.5z"/></svg>
        <span>+41 71 604 2893</span>
      </div>
      <div class="contact__row">
        <svg viewBox="0 0 16 16" fill="none" stroke="currentColor" stroke-width="1.5"><rect x="1.5" y="3" width="13" height="10" rx="1"/><polyline points="1.5,3.5 8,9 14.5,3.5"/></svg>
        <span>marco.lindt@veranix.ch</span>
      </div>
      <div class="contact__row">
        <svg viewBox="0 0 16 16" fill="none" stroke="currentColor" stroke-width="1.3"><circle cx="8" cy="8" r="6.5"/><ellipse cx="8" cy="8" rx="3" ry="6.5"/><line x1="1.5" y1="8" x2="14.5" y2="8"/></svg>
        <span>www.veranix.ch</span>
      </div>
    </div>
  </section>
</main>
</body>
</html>
```